Small legal and financial translation company needs Squarespace website, brochure and logo

Hello,
We are Lumarin Services (www.lumarinservices-example.com), a boutique legal and financial translation company. We offer our services mainly to Spanish customers. Our primary line of business is the translation of financial statements, but we translate a wide variety legal and financial texts.
The project we are offering comprises three parts: a redo of the current website, an informational brochure for potential customer and a logo design. These three parts should provide a consistent image. We would develop content soon.
We are looking for a website that would look like a typical law firm website, nothing too fancy. Right now, it is in English, Spanish and French, although the new site need only be in English and Spanish. There must be good toggling between the English and Spanish versions. There would be no need for tie-ins to social media and it would not contain a blog. Basically, a static site. We aren't interesting in driving traffic to the site or SEO, as we will contact nearly all potential customers beforehand. The website must be built in Squarespace to enable a smooth transition. The content would be similar to the current page, we'll be working on the exact content, but a rough draft is attached.
The brochure will be some three pages and would introduce the company to potential customers, using similar images as the website and the logo to be designed.
The only specifications for the logo is, as the website and brochure, it convey a sense of security and trust.
Feel free to ask with any questions as this is the first time we have used this platform.
Thank you!
Updates

I've added a more or less final version for the text in the brochure and updated the brief. Added Wednesday, June 10, 2015

Target Market(s)

Spanish law firms, auditors, accountants, banks, investment firms

Industry/Entity Type

Finance

Logo Text

Lumarin Services

Number of Pages Required

5+ page

Font styles to use
Serif

Requirements
Must have
• The website must be built in Squarespace and have a good option to toggle between English and Spanish versions.
• Brochure must be in both English and Spanish, I'm attaching a rough draft of the information that it will probably have. This should give an idea about what to include and the spacing. I will update it to include the final information.
Nice to have
• Would be nice to have some quality finance- and legal-related images
Should not have
• Vibrant colours

```html
<!DOCTYPE html>
<html lang="en">
<head>
<meta charset="utf-8">
<title>Lumarin Services – Brochure pages 3 &amp; 4</title>
<link rel="stylesheet" href="https://fonts.googleapis.com/css2?family=Cinzel:wght@400;600&family=EB+Garamond:ital,wght@0,400;0,700;1,400&display=swap">
<style>
  :root {
    --canvas: #e4e4e4;
    --paper: #ffffff;
    --ink: #2b2b2b;
    --ink-soft: #555555;
    --wine: #7d0f1e;
    --wine-dark: #4e0712;
    --night: #050505;
    --night-soft: #2a2a2a;
    --panel-top: #f4f4f4;
    --panel-bottom: #bdbdbd;
    --white: #ffffff;
  }
  * { box-sizing: border-box; margin: 0; padding: 0; }
  html, body { width: 1200px; height: 847px; overflow: hidden; }
  body {
    background: radial-gradient(ellipse at 50% 40%, #f3f3f3 0%, var(--canvas) 70%);
    font-family: "EB Garamond", Georgia, serif;
    color: var(--ink);
    position: relative;
  }
  .spread {
    position: absolute;
    left: 110px; top: 84px;
    width: 980px; height: 680px;
    display: flex;
    box-shadow: 0 18px 40px rgba(0,0,0,.25);
  }
  .page { position: relative; width: 490px; height: 680px; overflow: hidden; }

  /* Left page */
  .page--expertise { background: var(--paper); }
  .page__photo {
    position: absolute; left: 0; top: 0; width: 100%; height: 220px;
    background: linear-gradient(135deg, #cfcfcf 0%, #ededed 45%, #f7f7f7 70%, #dedede 100%);
  }
  .section-title {
    position: absolute; left: 40px; top: 244px;
    font-family: "Cinzel", "Times New Roman", serif;
    font-size: 21px; font-weight: 400; letter-spacing: 1px;
    color: var(--wine);
  }
  .expertise-list { position: absolute; left: 40px; top: 282px; width: 420px; list-style: none; }
  .expertise-item { display: flex; gap: 14px; margin-bottom: 28px; }
  .expertise-item__number {
    flex: 0 0 36px; height: 36px; margin-top: 22px;
    border: 1.5px solid var(--ink); border-radius: 50%;
    display: flex; align-items: center; justify-content: center;
    font-size: 19px;
  }
  .expertise-item__title { font-weight: 700; font-size: 14.5px; line-height: 1.2; margin-bottom: 2px; }
  .expertise-item__text { font-size: 12px; line-height: 1.28; color: var(--ink-soft); }

  /* Footer bands */
  .page__footer { position: absolute; left: 0; bottom: 0; width: 100%; height: 90px; }
  .page__footer svg { position: absolute; inset: 0; width: 100%; height: 100%; }
  .page__url {
    position: absolute; bottom: 20px;
    font-size: 17px; letter-spacing: .5px; color: var(--white);
  }
  .page--expertise .page__url { left: 30px; }
  .page--comparison .page__url { left: 24px; }

  /* Right page */
  .page--comparison {
    background: linear-gradient(100deg, var(--night) 0%, var(--night-soft) 55%, var(--night) 100%);
  }
  .comparison-title {
    position: absolute; left: 0; top: 26px; width: 100%;
    text-align: center;
    font-family: "Cinzel", "Times New Roman", serif;
    font-size: 19px; font-weight: 400; line-height: 1.2; letter-spacing: 1.5px;
    color: var(--white);
  }
  .comparison {
    position: absolute; left: 28px; top: 112px; width: 434px;
    display: flex; align-items: flex-start; gap: 10px;
  }
  .comparison__column { flex: 1; }
  .comparison__head {
    background: linear-gradient(180deg, #9a1426 0%, var(--wine) 100%);
    color: var(--white);
    font-size: 15px; font-weight: 400; text-align: center;
    padding: 7px 0; margin: 0 -4px;
  }
  .comparison__body {
    background: linear-gradient(180deg, var(--panel-top) 0%, var(--panel-bottom) 100%);
    padding: 18px 14px 20px;
    display: flex; flex-direction: column; gap: 22px;
  }
  .comparison--agency .comparison__body { padding-bottom: 40px; }
  .comparison__text { font-size: 11.5px; line-height: 1.25; color: var(--ink-soft); text-align: justify; }
</style>
</head>
<body>
  <main class="spread">
    <section class="page page--expertise">
      <div class="page__photo" role="img" aria-label="Black and white photo of a hand signing a document with a pen on a desk"></div>
      <h2 class="section-title">Areas of Expertise</h2>
      <ol class="expertise-list">
        <li class="expertise-item">
          <span class="expertise-item__number">1</span>
          <div>
            <h3 class="expertise-item__title">Duis autem vel eum iriure dolor</h3>
            <p class="expertise-item__text">Lorem ipsum dolor sit amet, consectetuer adipiscing elit, sed diam nonummy nibh euismod tincidunt ut laoreet dolore magna aliquam erat volutpat. Ut wisi enim ad minim veniam, quis nostrud exerci tation ullamcorper suscipit lobortis nisl ut aliquip ex ea commodo consequat.</p>
          </div>
        </li>
        <li class="expertise-item">
          <span class="expertise-item__number">2</span>
          <div>
            <h3 class="expertise-item__title">Duis autem vel eum iriure dolor</h3>
            <p class="expertise-item__text">Lorem ipsum dolor sit amet, consectetuer adipiscing elit, sed diam nonummy nibh euismod tincidunt ut laoreet dolore magna aliquam erat volutpat. Ut wisi enim ad minim veniam, quis nostrud exerci tation ullamcorper suscipit lobortis nisl ut aliquip ex ea commodo consequat.</p>
          </div>
        </li>
        <li class="expertise-item">
          <span class="expertise-item__number">3</span>
          <div>
            <h3 class="expertise-item__title">Duis autem vel eum iriure dolor</h3>
            <p class="expertise-item__text">Lorem ipsum dolor sit amet, consectetuer adipiscing elit, sed diam nonummy nibh euismod tincidunt ut laoreet dolore magna aliquam erat volutpat. Ut wisi enim ad minim veniam, quis nostrud exerci tation ullamcorper suscipit lobortis nisl ut aliquip ex ea commodo consequat.</p>
          </div>
        </li>
      </ol>
      <footer class="page__footer">
        <svg viewBox="0 0 490 90" preserveAspectRatio="none" aria-hidden="true">
          <defs>
            <linearGradient id="wineBandLeft" x1="0" x2="1">
              <stop offset="0" stop-color="#8a1022"/>
              <stop offset="1" stop-color="#5a0914"/>
            </linearGradient>
          </defs>
          <path d="M230 20 Q380 -4 490 6 L490 40 Q360 30 230 20 Z" fill="#0a0a0a"/>
          <path d="M0 32 Q250 10 490 36 L490 90 L0 90 Z" fill="url(#wineBandLeft)"/>
        </svg>
        <p class="page__url">www.lumarinservices-example.com</p>
      </footer>
    </section>

    <section class="page page--comparison">
      <h2 class="comparison-title">Differences between working<br>with a translation agency<br>and a translation provider</h2>
      <div class="comparison">
        <div class="comparison__column comparison--agency">
          <h3 class="comparison__head">Translation Agency</h3>
          <div class="comparison__body">
            <p class="comparison__text">Lorem ipsum dolor sit amet, consectetuer adipiscing elit, sed diam nonummy nibh euismod tincidunt ut laoreet dolore magna aliquam erat volutpat. Ut wisi enim ad minim veniam, quis nostrud exerci tation ullamcorper suscipit lobortis nisl ut aliquip ex ea commodo consequat.</p>
            <p class="comparison__text">Lorem ipsum dolor sit amet, consectetuer adipiscing elit, sed diam nonummy nibh euismod tincidunt ut laoreet dolore magna aliquam erat volutpat. Ut wisi enim ad minim veniam, quis nostrud exerci tation ullamcorper suscipit lobortis nisl ut aliquip ex ea commodo consequat.</p>
            <p class="comparison__text">Lorem ipsum dolor sit amet, consectetuer adipiscing elit, sed diam nonummy nibh euismod tincidunt ut laoreet dolore magna aliquam erat volutpat. Ut wisi enim ad minim veniam, quis nostrud exerci tation ullamcorper suscipit lobortis nisl ut aliquip ex ea commodo consequat.</p>
          </div>
        </div>
        <div class="comparison__column comparison--provider">
          <h3 class="comparison__head">Translation Provider</h3>
          <div class="comparison__body">
            <p class="comparison__text">Lorem ipsum dolor sit amet, consectetuer adipiscing elit, sed diam nonummy nibh euismod tincidunt ut laoreet dolore magna aliquam erat volutpat. Ut wisi enim ad minim veniam, quis nostrud exerci tation ullamcorper suscipit lobortis nisl ut aliquip ex ea commodo consequat.</p>
            <p class="comparison__text">Lorem ipsum dolor sit amet, consectetuer adipiscing elit, sed diam nonummy nibh euismod tincidunt ut laoreet dolore magna aliquam erat volutpat. Ut wisi enim ad minim veniam, quis nostrud exerci tation ullamcorper suscipit lobortis nisl ut aliquip ex ea commodo consequat.</p>
            <p class="comparison__text">Lorem ipsum dolor sit amet, consectetuer adipiscing elit, sed diam nonummy nibh euismod tincidunt ut laoreet dolore magna aliquam erat volutpat. Ut wisi enim ad minim veniam, quis nostrud exerci tation ullamcorper suscipit lobortis nisl ut aliquip ex ea commodo consequat.</p>
          </div>
        </div>
      </div>
      <footer class="page__footer">
        <svg viewBox="0 0 490 90" preserveAspectRatio="none" aria-hidden="true">
          <defs>
            <linearGradient id="wineBandRight" x1="0" x2="1">
              <stop offset="0" stop-color="#5a0914"/>
              <stop offset="1" stop-color="#8a1022"/>
            </linearGradient>
          </defs>
          <path d="M0 36 Q240 10 490 22 L490 90 L0 90 Z" fill="url(#wineBandRight)"/>
        </svg>
        <p class="page__url">www.lumarinservices-example.com</p>
      </footer>
    </section>
  </main>
</body>
</html>
```